Business Card - Tidal Lanes

Need Business Card design for company named Tidal Lanes. Software development focused mainly on Brindle Orvix & Zelt Apps. I've attached our logo with both a black and white background. Please add trademark symbol to logo when using.

```html
<!DOCTYPE html>
<html lang="en">
<head>
<meta charset="utf-8">
<title>Tidal Lanes – Business Card</title>
<link rel="stylesheet" href="https://fonts.googleapis.com/css2?family=Source+Sans+3:wght@300;400;600;700&display=swap">
<style>
  :root {
    --page-bg: #e9e6e1;
    --card-dark: #2b2b2b;
    --card-mid: #474747;
    --card-light: #5a5a5a;
    --text-light: #f2f2f2;
    --text-muted: #d4d4d4;
    --text-dark: #262626;
    --band-orange: #f7941d;
    --band-yellow: #ffc20e;
    --accent-red: #d7261e;
    --icon-gold: #f5b41a;
  }
  * { box-sizing: border-box; margin: 0; padding: 0; }
  html, body { width: 1200px; height: 720px; overflow: hidden; }
  body {
    background: var(--page-bg);
    font-family: "Source Sans 3", Arial, sans-serif;
    position: relative;
  }
  .card {
    position: absolute;
    top: 205px;
    width: 540px;
    height: 309px;
    border-radius: 4px;
    overflow: hidden;
    background: linear-gradient(160deg, var(--card-dark) 0%, var(--card-mid) 45%, var(--card-dark) 70%, var(--card-light) 100%);
    box-shadow: 0 6px 18px rgba(0,0,0,0.25);
  }
  .card--front { left: 40px; }
  .card--back { left: 620px; }

  .wordmark {
    position: absolute;
    display: flex;
    align-items: center;
    gap: 8px;
    color: var(--text-light);
    font-weight: 700;
    letter-spacing: -0.5px;
    white-space: nowrap;
  }
  .wordmark__dot {
    width: 12px; height: 12px;
    border-radius: 50%;
    background: var(--band-orange);
  }
  .card--front .wordmark { left: 44px; top: 118px; font-size: 34px; }
  .card--back .wordmark { left: 50%; top: 112px; transform: translateX(-50%); font-size: 46px; }
  .card--back .wordmark__dot { width: 16px; height: 16px; }

  .divider {
    position: absolute;
    left: 272px; top: 40px;
    width: 1px; height: 108px;
    background: linear-gradient(to bottom, rgba(255,255,255,0), rgba(255,255,255,0.45), rgba(255,255,255,0));
  }
  .contact {
    position: absolute;
    left: 300px; top: 38px;
    color: var(--text-muted);
    font-size: 15px;
    font-weight: 400;
    line-height: 22px;
    list-style: none;
  }
  .contact li { display: flex; align-items: center; gap: 8px; }
  .contact svg { width: 12px; height: 12px; fill: var(--icon-gold); flex: none; }
  .contact .address { margin-top: 8px; padding-left: 20px; display: block; }

  .band { position: absolute; left: 0; top: 0; width: 540px; height: 309px; }

  .holder {
    position: absolute;
    left: 150px; top: 248px;
    width: 140px;
    text-align: center;
  }
  .holder__name { font-size: 18px; font-weight: 700; color: var(--text-dark); line-height: 20px; }
  .holder__title { font-size: 14px; font-weight: 400; color: var(--text-dark); line-height: 18px; }

  .website {
    position: absolute;
    left: 0; right: 0; top: 232px;
    text-align: center;
    color: var(--text-muted);
    font-size: 17px;
    font-weight: 400;
    letter-spacing: 4px;
  }
</style>
</head>
<body>
  <section class="card card--front" aria-label="Business card front">
    <svg class="band" viewBox="0 0 540 309" aria-hidden="true">
      <defs>
        <linearGradient id="bandFill" x1="0" y1="0" x2="1" y2="0">
          <stop offset="0" stop-color="#f7941d"/>
          <stop offset="0.55" stop-color="#ffb516"/>
          <stop offset="1" stop-color="#ffc20e"/>
        </linearGradient>
      </defs>
      <path d="M0,212 C140,224 300,200 400,166 C460,146 510,136 540,131 L540,152 C470,172 410,220 345,309 L0,309 Z" fill="url(#bandFill)"/>
      <path d="M0,206 C140,218 300,194 400,160 C460,140 510,130 540,125" fill="none" stroke="#d7261e" stroke-width="4"/>
      <path d="M250,200 C320,184 380,160 430,140 C480,122 515,116 540,113" fill="none" stroke="#d7261e" stroke-width="2"/>
    </svg>

    <div class="wordmark"><span class="wordmark__dot"></span>Tidal Lanes</div>
    <div class="divider"></div>

    <ul class="contact">
      <li>
        <svg viewBox="0 0 12 12"><path d="M3 0h6a1 1 0 0 1 1 1v10a1 1 0 0 1-1 1H3a1 1 0 0 1-1-1V1a1 1 0 0 1 1-1zm0 2v7h6V2z"/></svg>
        555-210-4471
      </li>
      <li>
        <svg viewBox="0 0 12 12"><path d="M2.5 3.5 3.5 1h5l1 2.5H11v5h-1v1.5H8.5V8.5h-5V10H2V8.5H1v-5zm1 0h5L8 2H4z"/></svg>
        555-638-0192
      </li>
      <li class="address">4820 Harbor Row<br>Marlow, FL 34012</li>
    </ul>

    <div class="holder">
      <p class="holder__name">Your Name</p>
      <p class="holder__title">Title</p>
    </div>
  </section>

  <section class="card card--back" aria-label="Business card back">
    <div class="wordmark"><span class="wordmark__dot"></span>Tidal Lanes</div>
    <p class="website">www.tidallanes.com</p>
  </section>
</body>
</html>
```